Design website home page for pathology consulting company

Starting a new consulting company with anatomic pathologists focused on expert diagnosis and second opinions on difficult pathology cases. In the near future we will be incorporating next generation diagnostics for rare diseases of childhood into the business. These include discovery and testing of DNA for mutations.

The company is formed around one of the best known pathologists in the world named Marcel "Biscuit" Trowell. The name of the company is "BiscuitLab"

We had a logo design by SketchForum - it is great. I will attach file as soon as I have it (contest ending today). Our company is medical, uses microscopes, DNA, probably will focus on childhood diseases but not solely on childhood diseases. we're not particularly conservative, but the customers we want to appeal to include older practicing pathologists as well as patients (sometimes parents) looking for second opinions.

Think a group of expert doctors diagnosing disease through the microscope and through DNA technology, ages ranging from 35-75 all trained by the best pathologist in the world - "Biscuit"

We receive glass slides from diseases from patients all over the world from docs who need an expert to tell them what is the diagnosis. So "path to the diagnosis" is also part of the company marketing message.

We want the website design to describe our company but be very simple to find what one is looking for as we will use it as the launch page to:
1) order services
2) check results/reports
3) set up new account
4) speak with one of the pathologists
5) see our test menu
6) access our educational material/webinars
Updates

Update - looking for home page design and then finalists will ask for second page design to keep with theme - ok?

Reason: realized this project isn't web design but web home page design - thanks

Reason: Holidays for some in next two weeks

Reason: Hot discussion among collaborators for a few of the submissions. Will provide detail individually this weekend. Thanks so much for all the submissions!

Target Market(s)

Referring pathologists, physicians who want second opinions on pathology disease diagnosis, patients who have had biopsies (either patients themselves or parents of patients), generally high education level

Industry/Entity Type

Marketing

Requirements
Must have
• BiscuitLab
Next Generation Pathology Consultants

```html
<!DOCTYPE html>
<html lang="en">
<head>
<meta charset="utf-8">
<title>BiscuitLab – Next Generation Pathology Consultants</title>
<link href="https://fonts.googleapis.com/css2?family=Open+Sans:wght@400;600;700&display=swap" rel="stylesheet">
<style>
:root{
  --page:#f0f0f0;
  --white:#ffffff;
  --blue:#1b84c8;
  --blue-dark:#0a62ad;
  --navy:#0b4a8d;
  --link:#1a5f99;
  --text:#333333;
  --muted:#9a9a9a;
  --rule:#e4e4e4;
  --panel:#ececec;
}
*{box-sizing:border-box;margin:0;padding:0}
html,body{width:1200px;height:1079px;overflow:hidden}
body{background:var(--page);font-family:"Open Sans",Arial,sans-serif;color:var(--text);position:relative}
.abs{position:absolute}
.footer-band{left:0;top:1013px;width:1200px;height:66px;background:var(--navy)}
.footer-band .copy{left:99px;top:37px;color:var(--white);font-size:12px}
.footer-band .social{right:99px;top:36px;color:var(--white);font-size:13px;font-weight:600}
.brand{left:99px;top:8px;width:170px;text-align:center}
.brand .mark{width:78px;height:78px;border-radius:50%;background:#c9c9c9;margin:0 auto 2px}
.brand .name{font-size:26px;color:var(--blue-dark);font-weight:400;line-height:28px;letter-spacing:.5px}
.brand .tag{font-size:8px;color:#777;line-height:10px}
.util{right:99px;top:47px;font-size:12px;color:#555;display:flex;gap:0}
.util span{padding:0 10px;border-left:1px solid #ddd;display:flex;align-items:center;gap:4px}
.util span:first-child{border-left:none}
.util svg{width:11px;height:11px;fill:var(--blue-dark)}
.order{right:99px;top:75px;font-size:16px;font-weight:700;color:#333}
.order b{color:var(--blue-dark);margin-left:6px;font-size:17px}
.sheet{left:99px;top:130px;width:1002px;height:910px;background:var(--white);border-radius:8px}
.nav{left:99px;top:130px;width:1002px;height:46px;display:flex;border-radius:8px 8px 0 0;overflow:hidden;background:linear-gradient(#1e95dd,#0b6cb8)}
.nav a{color:var(--white);text-decoration:none;font-size:13px;display:flex;align-items:center;justify-content:center;border-left:1px solid rgba(255,255,255,.18)}
.nav a.active{background:linear-gradient(#c5c5c5,#9b9b9b);border-left:none}
.hero{left:117px;top:193px;width:966px;height:310px;background:linear-gradient(90deg,#e8eef4 0%,#cfd9e3 40%,#b7c2cc 70%,#e2e2e2 100%)}
.hero h1{left:15px;top:10px;font-size:33px;color:var(--blue);font-weight:400}
.hero h2{left:15px;top:48px;font-size:23px;color:#8c8c8c;font-weight:400}
.card{top:522px;width:307px;height:114px;border-radius:0 0 9px 9px;background:linear-gradient(#1e8fd6,#0a64b2);color:var(--white);padding:12px 15px}
.card h3{font-size:17px;font-weight:600;margin-bottom:8px}
.card p{font-size:12px;line-height:16px;color:#cfe6f7;width:250px}
.card .play{right:16px;bottom:13px;width:36px;height:36px}
.services{left:117px;top:658px;width:196px}
.title{font-size:16px;font-weight:600;color:#333;text-transform:uppercase}
.services ul{list-style:none;margin-top:11px}
.services li{height:30px;border-bottom:1px solid var(--rule);font-size:11px;color:var(--link);display:flex;align-items:center;padding-left:19px;position:relative}
.services li:last-child{border-bottom:none}
.services li::before{content:"";position:absolute;left:1px;border-left:6px solid #bbb;border-top:4px solid transparent;border-bottom:4px solid transparent}
.vrule{width:1px;background:var(--rule);top:662px;height:352px}
.welcome{left:361px;top:658px;width:470px}
.welcome p{font-size:12.5px;line-height:21px;color:var(--muted);margin-top:10px;margin-bottom:21px}
.welcome .title+p{margin-top:14px}
.side{left:864px;top:662px;width:219px;height:357px;border-radius:9px;background:#2d7dd0;overflow:hidden}
.signup{height:243px;background:var(--panel);padding:16px 18px;border-radius:0 0 9px 9px}
.signup h4{font-size:17px;font-weight:400;color:#333;margin-bottom:14px}
.field{width:184px;height:33px;background:var(--white);border:1px solid #ddd;font-size:11.5px;color:#888;padding:8px 12px;margin-bottom:23px}
.btn-primary{display:block;margin:2px auto 0;width:132px;height:31px;background:var(--blue-dark);color:var(--white);font-size:15px;text-align:center;line-height:31px}
.forgot{text-align:center;font-size:11.5px;color:#888;margin-top:7px}
.btn-light{left:18px;top:259px;width:184px;height:33px;background:var(--white);border:1px solid #ccc;text-align:center;line-height:31px;color:#777;font-size:15px}
.btn-dark{left:18px;top:307px;width:184px;height:32px;background:#111;border:1px solid #888;text-align:center;line-height:30px;color:var(--white);font-size:15px}
</style>
</head>
<body>
<div class="abs footer-band">
  <div class="abs copy">Copyright © 2013 Consultants, Inc . All Rights Reserved</div>
  <div class="abs social">Follow us</div>
</div>

<div class="abs brand">
  <div class="mark"></div>
  <div class="name">BiscuitLab</div>
  <div class="tag">Next Generation Pathology Consultants</div>
</div>

<div class="abs util">
  <span><svg viewBox="0 0 10 10"><path d="M1 0h6l2 2v8H1z M3 4h4v1H3z M3 6h4v1H3z" fill-rule="evenodd"/></svg>Register</span>
  <span><svg viewBox="0 0 10 10"><circle cx="5" cy="3" r="2.5"/><path d="M0 10c0-3 2-4.5 5-4.5s5 1.5 5 4.5z"/></svg>Sign In</span>
  <span><svg viewBox="0 0 10 10"><path d="M0 3c2-2 8-2 10 0v2H7V4H3v1H0z M2 6h6l1 4H1z"/></svg>contact</span>
</div>
<div class="abs order">24/7 ORDER <b>080-5555-014</b></div>

<div class="abs sheet"></div>

<nav class="abs nav">
  <a class="active" style="width:91px">Home</a>
  <a style="width:122px">About Us</a>
  <a style="width:115px">Services</a>
  <a style="width:207px">Pathology Consultants</a>
  <a style="width:118px">Patients</a>
  <a style="width:109px">Results</a>
  <a style="width:120px">Accounts</a>
  <a style="width:120px">Contact Us</a>
</nav>

<section class="abs hero" role="img" aria-label="Two lab scientists in goggles examining a flask in a pathology laboratory">
  <h1 class="abs">BiscuitLab</h1>
  <h2 class="abs">Next Generation Pathology Consultants</h2>
</section>

<div class="abs card" style="left:117px">
  <h3>Surgical/Autopsy Pathology</h3>
  <p>Pathologic examination of surgical tissue specimens constitutes the major.</p>
  <svg class="abs play" viewBox="0 0 36 36"><circle cx="18" cy="18" r="17" fill="#d9d9d9" stroke="#aaa"/><path d="M14 10l12 8-12 8z" fill="#fff"/></svg>
</div>
<div class="abs card" style="left:447px">
  <h3>Cytopathology</h3>
  <p>The cytopathology laboratory at Pathology Consultants, PC is a full service.</p>
  <svg class="abs play" viewBox="0 0 36 36"><circle cx="18" cy="18" r="17" fill="#d9d9d9" stroke="#aaa"/><path d="M14 10l12 8-12 8z" fill="#fff"/></svg>
</div>
<div class="abs card" style="left:777px">
  <h3>Hematopathology</h3>
  <p>Pathologic examination of all hematolymphoid tissue specimens is performed.</p>
  <svg class="abs play" viewBox="0 0 36 36"><circle cx="18" cy="18" r="17" fill="#d9d9d9" stroke="#aaa"/><path d="M14 10l12 8-12 8z" fill="#fff"/></svg>
</div>

<section class="abs services">
  <div class="title">Our Services</div>
  <ul>
    <li>Autopsy Pathology</li>
    <li>Bone and Soft Tissue Pathology</li>
    <li>Clinically Interactive Consultative</li>
    <li>Dermatopathology</li>
    <li>Forensic Pathology</li>
    <li>Gastrointestinal &amp; Hepatic</li>
    <li>Hematology &amp; Hemato</li>
    <li>Immunopathology/Histopathology</li>
    <li>Pediatric Pathology</li>
    <li>Surgical Pathology</li>
    <li>Urologic Pathology</li>
  </ul>
</section>

<div class="abs vrule" style="left:339px"></div>

<section class="abs welcome">
  <div class="title">Welcome to BiscuitLab</div>
  <p>Sed ut perspiciatis unde omnis iste natus error sit voluptatem accusantium doloremque laudantium, totam rem aperiam, eaque ipsa quae ab illo inventore veritatis et quasi architecto beatae vitae dicta sunt explicabo.</p>
  <p>Nemo enim ipsam voluptatem quia voluptas sit aspernatur aut odit aut fugit, sed quia consequuntur.</p>
  <div class="title" style="margin-top:-2px">We Work for Your Health</div>
  <p>Sed ut perspiciatis unde omnis iste natus error sit voluptatem accusantium doloremque laudantium, totam rem aperiam, eaque ipsa quae ab illo inventore veritatis et quasi architecto beatae vitae dicta sunt explicabo.</p>
  <p>Nemo enim ipsam voluptatem quia voluptas sit aspernatur aut odit aut fugit, sed quia consequuntur magni dolores eos qui ratione voluptatem sequi nesciunt. Neque porro quisquam est, qui dolorem ipsum.</p>
</section>

<div class="abs vrule" style="left:847px"></div>

<aside class="abs side">
  <div class="signup">
    <h4>Setup New Account</h4>
    <div class="field">Enter your email</div>
    <div class="field">Enter password</div>
    <div class="btn-primary">SIGN UP</div>
    <div class="forgot">Forgot Password?</div>
  </div>
  <div class="abs btn-light">See Our Test Menu</div>
  <div class="abs btn-dark">Speek with Pathologist</div>
</aside>
</body>
</html>
```